New Business card design to reflect rebrand

I would like a business card design with a good base colour for our new logo and also a placeholder for a profile pic of the card holder. the design needs to be editable to the point that we can easily change the picture of the person and use that design for printmerlo etc. we are looking at a metalic finish business card so will need a good base colour to bring out the finish.

Target Market(s)

prospective customers

Industry/Entity Type

Business

Contact Information for Business Card

I would like one editable design that we can change the name of the card holder and profile picture. The design need to be in a format that be send to printmerlo etc.

Our address is Fenwick Lodge, Copse Lane, Hartley Wintney, GU14 3TP Tel no. 01483 556172

Requirements
Must have
• place holder for a profile pic for the card holder. in AI or preferably PSD format

```html
<!DOCTYPE html>
<html lang="en">
<head>
<meta charset="utf-8">
<title>Norland Office Solutions — Business Card</title>
<link rel="stylesheet" href="https://fonts.googleapis.com/css2?family=Lato:wght@400;700;900&display=swap">
<style>
  :root {
    --orange: #e8620c;
    --navy: #3f5472;
    --white: #ffffff;
    --page: #f4f4f4;
  }
  * { box-sizing: border-box; margin: 0; padding: 0; }
  html, body { width: 1200px; height: 1200px; overflow: hidden; }
  body {
    background: var(--page);
    font-family: "Lato", sans-serif;
    position: relative;
  }
  .card {
    position: absolute;
    left: 180px;
    width: 840px;
    height: 480px;
    background: var(--orange);
    box-shadow: 0 10px 30px rgba(0,0,0,0.12);
  }
  .card--back { top: 70px; }
  .card--front { top: 640px; }
  .card__panel {
    position: absolute;
    inset: 30px;
    background: var(--white);
    border-radius: 30px;
    overflow: hidden;
  }
  .card__band {
    position: absolute;
    left: 0; right: 0; bottom: 0;
    background: var(--navy);
  }
  .card--back .card__band { height: 54px; }
  .card--front .card__band { height: 180px; }

  .brand {
    position: absolute;
    display: flex;
    align-items: center;
    gap: 18px;
    color: var(--navy);
    font-weight: 900;
    text-transform: uppercase;
    line-height: 1;
  }
  .brand__mark {
    width: 26px; height: 26px;
    background: var(--orange);
    flex: none;
  }
  .brand__name { display: flex; flex-direction: column; }
  .card--back .brand { left: 0; right: 0; top: 150px; justify-content: center; }
  .card--back .brand__name { font-size: 62px; letter-spacing: 1px; }
  .card--back .brand__name span + span { font-size: 32px; letter-spacing: 7.5px; margin-top: 12px; }
  .card--front .brand { left: 40px; top: 76px; }
  .card--front .brand__name { font-size: 44px; letter-spacing: 1px; }
  .card--front .brand__name span + span { font-size: 22.5px; letter-spacing: 5.5px; margin-top: 10px; }

  .website-line {
    position: absolute;
    left: 0; right: 0; bottom: 0;
    height: 54px;
    line-height: 54px;
    text-align: center;
    color: var(--white);
    font-size: 21px;
    letter-spacing: 5px;
  }

  .photo {
    position: absolute;
    left: 510px; top: 56px;
    width: 204px; height: 206px;
    border: 3px solid var(--navy);
    border-radius: 12px;
    background: linear-gradient(180deg, #f2f2f2 0%, #e2ddd8 55%, #2b2b2e 100%);
  }

  .contacts {
    position: absolute;
    left: 24px; top: 285px;
    list-style: none;
    color: var(--white);
    font-size: 17px;
  }
  .contacts__row { display: flex; align-items: center; height: 46px; }
  .contacts__row--address { height: 40px; }
  .contacts__item { display: flex; align-items: center; gap: 14px; }
  .contacts__item--first { width: 226px; }
  .icon {
    width: 24px; height: 24px;
    border-radius: 50%;
    background: var(--orange);
    display: flex; align-items: center; justify-content: center;
    flex: none;
  }
  .icon svg { width: 14px; height: 14px; }
  .contacts__address { font-size: 14px; }

  .holder {
    position: absolute;
    left: 462px; top: 292px;
    width: 300px;
    text-align: center;
  }
  .holder__name { color: var(--white); font-size: 26px; font-weight: 700; line-height: 30px; }
  .holder__title { color: var(--orange); font-size: 17px; line-height: 20px; margin-top: 12px; }
</style>
</head>
<body>

<section class="card card--back" aria-label="Business card back">
  <div class="card__panel">
    <div class="brand">
      <div class="brand__mark"></div>
      <div class="brand__name"><span>Norland</span><span>Office Solutions</span></div>
    </div>
    <div class="card__band"></div>
    <p class="website-line">www.website.com</p>
  </div>
</section>

<section class="card card--front" aria-label="Business card front">
  <div class="card__panel">
    <div class="brand">
      <div class="brand__mark"></div>
      <div class="brand__name"><span>Norland</span><span>Office Solutions</span></div>
    </div>
    <div class="card__band"></div>
    <div class="photo" role="img" aria-label="Profile photo of the card holder"></div>

    <ul class="contacts">
      <li class="contacts__row">
        <span class="contacts__item contacts__item--first">
          <span class="icon"><svg viewBox="0 0 14 14"><rect x="4" y="1.5" width="6" height="11" rx="1" fill="none" stroke="#fff" stroke-width="1.4"/></svg></span>
          + 000 - 000 - 000
        </span>
        <span class="contacts__item">
          <span class="icon"><svg viewBox="0 0 14 14"><rect x="2" y="3.5" width="10" height="7" fill="none" stroke="#fff" stroke-width="1.3"/><path d="M2 3.5l5 4 5-4" fill="none" stroke="#fff" stroke-width="1.3"/></svg></span>
          mail@website.com
        </span>
      </li>
      <li class="contacts__row">
        <span class="contacts__item contacts__item--first">
          <span class="icon"><svg viewBox="0 0 14 14"><path d="M4 2l2 3-1.2 1.2c.6 1.3 1.7 2.4 3 3L9 8l3 2-1 2C6.5 12 2 7.5 2 3z" fill="#fff"/></svg></span>
          + 000 - 000 - 000
        </span>
        <span class="contacts__item">
          <span class="icon"><svg viewBox="0 0 14 14"><circle cx="7" cy="7" r="5" fill="none" stroke="#fff" stroke-width="1.2"/><ellipse cx="7" cy="7" rx="2.2" ry="5" fill="none" stroke="#fff" stroke-width="1"/><path d="M2 7h10" stroke="#fff" stroke-width="1"/></svg></span>
          www.website.com
        </span>
      </li>
      <li class="contacts__row contacts__row--address">
        <span class="contacts__item">
          <span class="icon"><svg viewBox="0 0 14 14"><path d="M7 13s-4-4.3-4-7a4 4 0 018 0c0 2.7-4 7-4 7z" fill="#fff"/><circle cx="7" cy="6" r="1.5" fill="#e8620c"/></svg></span>
          <span class="contacts__address">Address: Street No, Nord Avenue, Co,City/State Zipcode</span>
        </span>
      </li>
    </ul>

    <div class="holder">
      <p class="holder__name">CARD HOLDER NAME</p>
      <p class="holder__title">JOB TITLE</p>
    </div>
  </div>
</section>

</body>
</html>
```